Kestrel Facilities Business Card Design

We would now like to design business cards with the new Kestrel Facilities logo

Target Market(s)

Professional

Industry/Entity Type

Professional services

Contact Information for Business Card

Employee name, title, phone number, email address, corporate office address and logo.

Font styles to use
Sans Serif

Colors
0054AA
0677BA
7BADD7
CADEEF
E8F1F8

Requirements
Must have
• My logo
Should not have
• any other pictures or images besides my logo

```html
<!DOCTYPE html>
<html lang="en">
<head>
<meta charset="utf-8">
<title>Kestrel Facilities Business Card</title>
<link rel="stylesheet" href="https://fonts.googleapis.com/css2?family=Oswald:wght@500&family=Lato:wght@400&display=swap">
<style>
  :root {
    --bg: #2a2a2c;
    --card: #1c1d1f;
    --card-back-top: #2b2c2f;
    --card-back-bottom: #111214;
    --blue: #0677ba;
    --blue-bright: #0a7fe0;
    --text: #f2f2f2;
    --rule: #55575b;
    --icon-ink: #1c1d1f;
  }
  html, body {
    margin: 0;
    padding: 0;
    width: 1200px;
    height: 1108px;
    overflow: hidden;
    background: var(--bg);
  }
  .canvas {
    position: relative;
    width: 1200px;
    height: 1108px;
    display: flex;
    justify-content: center;
    align-items: center;
    gap: 100px;
  }
  .card {
    width: 400px;
    height: 700px;
    border-radius: 18px;
    box-shadow: 0 18px 40px rgba(0,0,0,0.45);
    position: relative;
    overflow: hidden;
  }
  .card-front {
    background: var(--card);
    display: flex;
    flex-direction: column;
    align-items: center;
    font-family: "Lato", sans-serif;
    color: var(--text);
  }
  .brand {
    margin-top: 110px;
    display: flex;
    align-items: center;
    gap: 18px;
  }
  .brand-square {
    width: 70px;
    height: 70px;
    background: var(--blue-bright);
    flex: none;
  }
  .brand-name {
    font-family: "Oswald", sans-serif;
    font-weight: 500;
    color: var(--blue-bright);
    font-size: 40px;
    line-height: 1.05;
    letter-spacing: 1px;
    text-transform: uppercase;
  }
  .person-name {
    margin-top: 110px;
    font-family: "Oswald", sans-serif;
    font-weight: 500;
    font-size: 34px;
    color: var(--blue-bright);
    text-transform: uppercase;
    letter-spacing: 0.5px;
    line-height: 1;
  }
  .person-title {
    margin-top: 6px;
    font-size: 20px;
  }
  .icon-row {
    margin-top: 18px;
    display: flex;
    align-items: center;
    gap: 8px;
    width: 270px;
  }
  .icon-row .rule {
    flex: 1;
    height: 1px;
    background: var(--rule);
  }
  .icon {
    width: 30px;
    height: 30px;
    border-radius: 4px;
    background: var(--blue-bright);
    display: flex;
    align-items: center;
    justify-content: center;
  }
  .contacts {
    margin-top: 14px;
    text-align: center;
    font-size: 20px;
    line-height: 1.45;
  }
  .divider {
    margin-top: 16px;
    width: 270px;
    height: 1px;
    background: var(--rule);
  }
  .address {
    margin-top: 14px;
    text-align: center;
    font-size: 20px;
    line-height: 1.45;
  }
  .card-back {
    background: linear-gradient(160deg, var(--card-back-top), var(--card-back-bottom) 65%);
  }
  .back-texture {
    position: absolute;
    inset: 0;
  }
  .back-brand {
    position: absolute;
    right: 70px;
    bottom: 110px;
    display: flex;
    align-items: center;
    gap: 8px;
  }
  .back-brand .brand-square {
    width: 22px;
    height: 22px;
  }
  .back-brand .brand-name {
    font-size: 16px;
  }
</style>
</head>
<body>
<main class="canvas">
  <section class="card card-front">
    <div class="brand">
      <div class="brand-square"></div>
      <div class="brand-name">Kestrel<br>Facilities</div>
    </div>
    <div class="person-name">Daniel Morrow</div>
    <div class="person-title">Managing Director</div>
    <div class="icon-row">
      <span class="rule"></span>
      <span class="icon">
        <svg width="18" height="18" viewBox="0 0 24 24"><path fill="var(--icon-ink)" d="M6.6 10.8a15 15 0 0 0 6.6 6.6l2.2-2.2a1 1 0 0 1 1-.25 11.4 11.4 0 0 0 3.6.57 1 1 0 0 1 1 1V20a1 1 0 0 1-1 1A17 17 0 0 1 3 4a1 1 0 0 1 1-1h3.5a1 1 0 0 1 1 1c0 1.25.2 2.45.57 3.57a1 1 0 0 1-.25 1z"/></svg>
      </span>
      <span class="icon">
        <svg width="18" height="18" viewBox="0 0 24 24"><rect x="3" y="5" width="18" height="14" rx="1" fill="none" stroke="var(--icon-ink)" stroke-width="2"/><path d="M3 6l9 7 9-7" fill="none" stroke="var(--icon-ink)" stroke-width="2"/></svg>
      </span>
      <span class="icon">
        <svg width="18" height="18" viewBox="0 0 24 24"><circle cx="12" cy="12" r="9" fill="none" stroke="var(--icon-ink)" stroke-width="2"/><path d="M3 12h18M12 3c3 3 3 15 0 18M12 3c-3 3-3 15 0 18" fill="none" stroke="var(--icon-ink)" stroke-width="1.6"/></svg>
      </span>
      <span class="rule"></span>
    </div>
    <div class="contacts">
      044-555 018 274<br>
      info@kestrelfm.com<br>
      www.kestrelfm.com
    </div>
    <div class="divider"></div>
    <div class="address">
      27 Harbour Row, Suite 4<br>
      Leeds LS1 4AP, England
    </div>
  </section>

  <section class="card card-back">
    <div class="back-texture" role="img" aria-label="Glossy tone-on-tone repeating brand pattern across the card back"></div>
    <div class="back-brand">
      <div class="brand-square"></div>
      <div class="brand-name">Kestrel Facilities</div>
    </div>
  </section>
</main>
</body>
</html>
```